Lagerverkauf
Zielgruppe
Textil Großhandel mit bekleidung bekannter Marken wie Korvane, Tundolux, Miro jeans etc..
Aufgabenstellung
Flyer DIn lang für einen Lagerverkauf von markenbekleidung, einfach gehalten, sehr clean, kein schnick schnack..
Marken: Tundolux, Korvane, Miro jeans, Vek, Bluvintex, Falkå, Edwin Marlow, Trove...etc
Inhalt Verkauf von z.B 4.09.2014 - 6.09.2014
Öffnungszeiten Do - 10 - 18 uhr, Fr - 10 - 18 Uhr, Sa 10 - 16 Uhr
Adresse Platzhalter

```html
<!DOCTYPE html>
<html lang="de">
<head>
<meta charset="utf-8">
<title>Markenbekleidung Lagerverkauf</title>
<link rel="stylesheet" href="https://fonts.googleapis.com/css2?family=Didact+Gothic&family=Questrial&display=swap">
<style>
  :root {
    --paper: #fdfcf8;
    --paper-warm: #f8f0e1;
    --ink: #1e1e1e;
    --ink-soft: #555555;
    --photo-light: #f4f2ee;
    --photo-mid: #c9c6c1;
    --photo-accent: #e6d96a;
  }
  html, body {
    margin: 0;
    padding: 0;
    width: 1200px;
    height: 566px;
    overflow: hidden;
  }
  .flyer {
    position: relative;
    width: 1200px;
    height: 566px;
    overflow: hidden;
    background: linear-gradient(180deg, var(--paper) 0%, var(--paper) 45%, var(--paper-warm) 100%);
    font-family: "Didact Gothic", sans-serif;
    color: var(--ink);
  }
  .campaign-photo {
    position: absolute;
    left: 505px;
    top: 165px;
    width: 695px;
    height: 401px;
    background:
      radial-gradient(ellipse 22% 30% at 68% 42%, var(--photo-accent) 0%, rgba(230,217,106,0) 100%),
      radial-gradient(ellipse 60% 70% at 60% 60%, var(--photo-mid) 0%, rgba(201,198,193,0) 100%),
      var(--photo-light);
    -webkit-mask-image: linear-gradient(90deg, transparent 0%, #000 12%, #000 90%, transparent 100%);
            mask-image: linear-gradient(90deg, transparent 0%, #000 12%, #000 90%, transparent 100%);
  }
  .headline {
    position: absolute;
    left: 0;
    top: 0;
  }
  .headline text {
    font-family: "Didact Gothic", sans-serif;
  }
  .kicker { font-size: 40px; fill: var(--ink); }
  .title { font-size: 89px; fill: var(--ink-soft); }
  .dates { font-size: 37px; fill: var(--ink); }
  .brands { font-size: 19px; fill: var(--ink); }
  .info {
    position: absolute;
    left: 48px;
    margin: 0;
  }
  .info-label {
    font-family: "Questrial", sans-serif;
    font-weight: 700;
    font-size: 17px;
    letter-spacing: 0.5px;
    margin: 0;
    line-height: 20px;
    -webkit-text-stroke: 0.5px var(--ink);
  }
  .location { top: 308px; }
  .location p { margin: 4px 0 0; font-size: 18px; }
  .hours { top: 386px; }
  .hours table {
    border-collapse: collapse;
    margin-top: 2px;
    font-size: 18px;
  }
  .hours td {
    padding: 0;
    height: 21.5px;
    vertical-align: baseline;
  }
  .hours .day { width: 101px; }
</style>
</head>
<body>
<main class="flyer">
  <div class="campaign-photo" role="img" aria-label="Modefoto: Model in gestreifter Hose, gelbem Top und roten Pumps auf einem silbernen Barocksessel mit Fußhocker"></div>

  <svg class="headline" width="1200" height="250" viewBox="0 0 1200 250" aria-label="Markenbekleidung Lagerverkauf">
    <text class="kicker" x="47" y="84">Markenbekleidung</text>
    <text class="title" x="44" y="159" textLength="652" lengthAdjust="spacingAndGlyphs">LAGERVERKAUF</text>
    <text class="dates" x="48" y="199" textLength="649" lengthAdjust="spacingAndGlyphs">4. SEPTEMBER 2014 - 6. SEPTEMBER 2014</text>
    <text class="brands" x="46" y="234" textLength="651" lengthAdjust="spacing">Tundolux | Korvane | Miro jeans | Vek | Bluvintex | Falkå | Edwin Marlow | Trove | u.v.m.</text>
  </svg>

  <section class="info location">
    <h2 class="info-label">WO?</h2>
    <p>Musterstraße 34 | 121234 Musterstadt</p>
  </section>

  <section class="info hours">
    <h2 class="info-label">WANN?</h2>
    <table>
      <tr><td class="day">Donnerstag:</td><td>10:00 - 18:00 Uhr</td></tr>
      <tr><td class="day">Freitag:</td><td>10:00 - 18:00 Uhr</td></tr>
      <tr><td class="day">Samstag:</td><td>10:00 - 16:00 uhr</td></tr>
    </table>
  </section>
</main>
</body>
</html>
```